Tech business card design

We need an amazing business card design for our new business 'Pexla' a marketing tech startup based in Sydney, Australia. We provide an online marketplace for businesses to search and buy advertising media, connect with service providers and learn more about marketing. We wish to communicate 'cool tech', reliability and professionalism and design based around our logo.

Target Market(s)

Business Owners

Contact Information for Business Card

Name
Position
Email Address
Website
Phone Number

Font styles to use
Other font styles liked:
• Avenir & Avenir Next

Colors

Designer to choose colors to be used in the design.

```html
<!DOCTYPE html>
<html lang="en">
<head>
<meta charset="utf-8">
<title>Pexla Business Card</title>
<link rel="stylesheet" href="https://fonts.googleapis.com/css2?family=Nunito+Sans:wght@400;600;700;900&display=swap">
<style>
  :root {
    --navy: #15183f;
    --ink: #1d1f3a;
    --paper: #ffffff;
    --stage: #222226;
    --muted: #3a3c55;
  }
  * { margin: 0; padding: 0; box-sizing: border-box; }
  html, body { width: 1200px; height: 800px; overflow: hidden; }
  body {
    background: var(--stage);
    font-family: "Nunito Sans", Arial, sans-serif;
    display: flex;
    align-items: center;
    justify-content: center;
    gap: 60px;
  }
  .card {
    width: 525px;
    height: 300px;
    background: var(--paper);
    position: relative;
    overflow: hidden;
    box-shadow: 0 18px 40px rgba(0,0,0,.45);
  }
  /* Front */
  .card-front {
    display: flex;
    flex-direction: column;
    align-items: center;
    justify-content: center;
  }
  .brand-name {
    font-weight: 900;
    color: var(--navy);
    letter-spacing: -2px;
    line-height: 1;
  }
  .card-front .brand-name { font-size: 92px; }
  .front-web {
    margin-top: 14px;
    font-size: 12px;
    font-weight: 700;
    letter-spacing: 6px;
    color: var(--ink);
  }
  /* Back */
  .back-band {
    position: absolute;
    left: 0; top: 0; bottom: 0;
    width: 150px;
    background: var(--navy);
    display: flex;
    align-items: center;
    justify-content: center;
  }
  .back-band .brand-name {
    color: var(--paper);
    font-size: 76px;
    transform: rotate(-90deg);
    white-space: nowrap;
  }
  .back-info {
    position: absolute;
    left: 178px; top: 0; right: 0; bottom: 0;
    color: var(--ink);
  }
  .name-row {
    position: absolute;
    top: 92px; left: 0; right: 0;
    display: flex;
    align-items: flex-end;
    gap: 10px;
  }
  .person-name { font-size: 17px; font-weight: 700; line-height: 1; }
  .name-rule { flex: 1; height: 1.5px; background: var(--navy); margin-bottom: 3px; }
  .person-role { position: absolute; top: 112px; font-size: 12px; font-weight: 600; }
  .address { position: absolute; top: 148px; font-size: 13px; line-height: 1.25; }
  .contacts { position: absolute; top: 218px; list-style: none; font-size: 12.5px; }
  .contacts li { display: flex; align-items: center; gap: 7px; margin-bottom: 3px; }
  .contacts svg { width: 14px; height: 14px; flex: none; }
  .contacts strong { font-weight: 700; }
</style>
</head>
<body>
  <section class="card card-front">
    <div class="brand-name">Pexla</div>
    <div class="front-web">www.pexlaweb.com</div>
  </section>

  <section class="card card-back">
    <div class="back-band"><div class="brand-name">Pexla</div></div>
    <div class="back-info">
      <div class="name-row">
        <span class="person-name">Mara Kell</span>
        <span class="name-rule"></span>
      </div>
      <div class="person-role">Manager</div>
      <p class="address">PO BOX 48, Harbour Lane<br>7th street Sydney<br>Australia</p>
      <ul class="contacts">
        <li>
          <svg viewBox="0 0 14 14" aria-hidden="true"><circle cx="7" cy="7" r="7" fill="#15183f"/><path d="M4.6 3.8l1.3 1.3-.7.9c.5 1 1.3 1.8 2.3 2.3l.9-.7 1.3 1.3-.8.9C6.8 9.6 4.4 7.2 3.8 5.1z" fill="#fff"/></svg>
          555.014.2290
        </li>
        <li>
          <svg viewBox="0 0 14 14" aria-hidden="true"><circle cx="7" cy="7" r="7" fill="#15183f"/><rect x="3.6" y="4.6" width="6.8" height="4.8" fill="none" stroke="#fff" stroke-width=".9"/><path d="M3.6 4.8L7 7.4l3.4-2.6" fill="none" stroke="#fff" stroke-width=".9"/></svg>
          hello@pexlamail.com
        </li>
        <li>
          <svg viewBox="0 0 14 14" aria-hidden="true"><circle cx="7" cy="7" r="7" fill="#15183f"/><circle cx="7" cy="7" r="3.6" fill="none" stroke="#fff" stroke-width=".8"/><path d="M3.4 7h7.2M7 3.4v7.2" stroke="#fff" stroke-width=".7"/></svg>
          <span>www.<strong>pexlaweb</strong>.com</span>
        </li>
      </ul>
    </div>
  </section>
</body>
</html>
```